Structural Engineering Business Card

Brookvane Drafting does residential house plans for clients in Central Florida. Would like simple but elegant business card that is appropriate for a house plan engineering company. Prefer black business card with black/white them but open to other shades of blue. I uploaded a sample card that I came across that looked good but please come up with your own creative designs.

Contact Information for Business Card

Name, Title, Phone, Email, Address, website

```html
<!DOCTYPE html>
<html lang="en">
<head>
<meta charset="utf-8">
<title>Brookvane Drafting — Business Card</title>
<link href="https://fonts.googleapis.com/css2?family=Arimo:wght@400;700&display=swap" rel="stylesheet">
<style>
  :root {
    --stage: #d9d9d9;
    --card: #1c1c1c;
    --ink: #ffffff;
    --ink-soft: #cfcfcf;
    --feature: #f4f4f4;
  }
  * { box-sizing: border-box; margin: 0; padding: 0; }
  html, body { width: 1200px; height: 800px; overflow: hidden; }
  body {
    background: var(--stage);
    font-family: "Arimo", Arial, sans-serif;
    display: flex;
    align-items: center;
    justify-content: center;
    gap: 40px;
  }
  .card {
    position: relative;
    width: 540px;
    height: 310px;
    background: var(--card);
    border-radius: 22px;
    color: var(--ink);
    overflow: hidden;
  }

  /* Contact side */
  .card__feature {
    position: absolute;
    left: 70px;
    top: 20px;
    width: 430px;
    height: 76px;
    background: var(--feature);
    border-radius: 14px;
  }
  .contact {
    position: absolute;
    left: 34px;
    bottom: 24px;
    font-size: 12.5px;
    line-height: 1.3;
    color: var(--ink-soft);
  }
  .contact__name {
    font-weight: 700;
    font-size: 17px;
    letter-spacing: 0.5px;
    text-transform: uppercase;
    color: var(--ink);
  }
  .contact__title { margin-bottom: 8px; }
  .contact__address { margin-bottom: 7px; }
  .contact__row { display: flex; align-items: center; gap: 8px; }
  .contact__row svg { width: 12px; height: 12px; flex: none; }
  .contact__web { margin-top: 8px; }

  /* Brand side */
  .brand {
    position: absolute;
    inset: 0;
    padding: 0 48px;
    display: flex;
    align-items: center;
    justify-content: center;
    gap: 12px;
  }
  .brand__mark {
    width: 20px;
    height: 20px;
    background: var(--ink);
    flex: none;
  }
  .brand__name {
    font-weight: 700;
    font-size: 32px;
    letter-spacing: 0.5px;
    text-transform: uppercase;
    white-space: nowrap;
  }
</style>
</head>
<body>

  <section class="card card--contact">
    <div class="card__feature" role="img" aria-label="Large white state map silhouette"></div>
    <div class="contact">
      <p class="contact__name">Daniel Harlow</p>
      <p class="contact__title">Managing Director</p>
      <p class="contact__address">4120 Cedar Ridge Way<br>Orlando, Florida 32801</p>
      <p class="contact__row">
        <svg viewBox="0 0 12 12" aria-hidden="true"><path d="M2.5 1h2l1 2.5-1.3 1a6 6 0 0 0 3.3 3.3l1-1.3L11 7.5v2a1 1 0 0 1-1 1A9 9 0 0 1 1.5 2a1 1 0 0 1 1-1z" fill="#fff"/></svg>
        407-555-0182
      </p>
      <p class="contact__row">
        <svg viewBox="0 0 12 12" aria-hidden="true"><rect x="2.5" y="0.8" width="7" height="10.4" rx="1.2" fill="none" stroke="#fff" stroke-width="1.2"/></svg>
        407-555-0147
      </p>
      <p class="contact__row">
        <svg viewBox="0 0 12 12" aria-hidden="true"><rect x="0.8" y="2.2" width="10.4" height="7.6" fill="#fff"/><path d="M0.8 2.2 6 6.5l5.2-4.3" fill="none" stroke="#1c1c1c" stroke-width="1"/></svg>
        info@brookvanedrafting.com
      </p>
      <p class="contact__web">www.brookvanedrafting.com</p>
    </div>
  </section>

  <section class="card card--brand">
    <div class="brand">
      <span class="brand__mark" aria-hidden="true"></span>
      <span class="brand__name">Brookvane Drafting</span>
    </div>
  </section>

</body>
</html>
```